Harbourline Physiotherapy business card design

We need a fresh, new business card design for our physiotherapy clinic Harbourline Physiotherapy

Will attach logo soon we had logo designed from our last project

Industry/Entity Type

Physical Therapy

Contact Information for Business Card

On front
Needs our logo, contact details:
58 Wexley Lane Brooksvale NSW 2841
Ph/f: 02 9481 2057
info@harbourlinephysio.example.com.au

Requirements
Must have
• On the back of the card needs to have area to write down follow up appointments
• On front
• Needs our logo
• The colours have to be the colours in our logo which are: sky blue, black and white
• Font to be same as our logo please
• We want the card to look simple, not too cluttered but to the point
Should not have
• We don't need any extra pictures other than our logo

```html
<!DOCTYPE html>
<html lang="en">
<head>
<meta charset="utf-8">
<title>Harbourline Physiotherapy – Business Card</title>
<link href="https://fonts.googleapis.com/css2?family=Open+Sans:ital,wght@0,400;0,600;0,700;1,400&display=swap" rel="stylesheet">
<style>
  :root {
    --canvas: #e9ebef;
    --royal: #2b2fa6;
    --royal-deep: #1d1f7a;
    --sky: #2aa7e0;
    --brand-blue: #1f4fc0;
    --charcoal: #3b3c40;
    --ink: #2a2a2e;
    --muted: #6c6e78;
    --white: #ffffff;
    --rule: #9aa0b0;
  }
  * { box-sizing: border-box; margin: 0; padding: 0; }
  html, body {
    width: 1200px; height: 950px; overflow: hidden;
    background: var(--canvas);
    font-family: "Open Sans", Arial, sans-serif;
  }
  .sheet {
    width: 1200px; height: 950px;
    display: flex; flex-direction: column; align-items: center; justify-content: center;
    gap: 40px;
  }
  .card {
    position: relative;
    width: 680px; height: 416px;
    border-radius: 4px;
    overflow: hidden;
    background: var(--white);
    box-shadow: 0 10px 30px rgba(20, 24, 60, .18);
  }

  /* ---------- Front ---------- */
  .card-front .backdrop {
    position: absolute; inset: 0;
    background: radial-gradient(ellipse 60% 55% at 28% 40%, var(--sky) 0%, var(--royal) 55%, var(--royal-deep) 100%);
  }
  .card-front .swoosh { position: absolute; inset: 0; width: 100%; height: 100%; }
  .brand {
    position: absolute; left: 400px; top: 62px;
    display: flex; align-items: center; gap: 12px;
    color: var(--brand-blue); font-weight: 600;
  }
  .brand-dot {
    width: 34px; height: 34px; border-radius: 50%;
    background: var(--brand-blue); flex: none;
  }
  .brand-name { line-height: 1.05; }
  .brand-name .line-1 { display: block; font-size: 30px; }
  .brand-name .line-2 { display: block; font-size: 19px; letter-spacing: .5px; }

  .holder {
    position: absolute; left: 40px; top: 250px; color: var(--white);
  }
  .holder-name { font-size: 22px; font-weight: 600; }
  .holder-role { font-size: 14px; opacity: .9; margin-top: 2px; }

  .contact {
    position: absolute; left: 210px; top: 250px; color: var(--white);
    font-size: 13px; line-height: 1.55; list-style: none;
  }
  .contact .address { margin-bottom: 14px; }
  .contact li { display: flex; align-items: center; gap: 8px; }
  .contact svg { width: 12px; height: 12px; flex: none; fill: var(--white); }

  /* ---------- Back ---------- */
  .card-back {
    padding: 40px 46px 52px; color: var(--ink);
    display: flex; flex-direction: column; justify-content: space-between;
  }
  .appt-title {
    text-align: right; color: var(--brand-blue);
    font-size: 26px; font-weight: 700;
  }
  .field-row { display: flex; align-items: flex-end; gap: 10px; font-size: 15px; }
  .fill-line { flex: 1; border-bottom: 2px dotted var(--rule); height: 18px; }
  .time-row .label { color: var(--brand-blue); font-weight: 600; }
  .time-row .fill-line { flex: 0 0 220px; }
  .time-row .unit { color: var(--brand-blue); font-size: 12px; }
  .days { display: flex; justify-content: space-between; list-style: none; }
  .days li { display: flex; align-items: center; gap: 6px; color: var(--brand-blue); font-size: 15px; }
  .tick-box { width: 15px; height: 15px; border: 1.5px solid var(--ink); }
  .policy { font-style: italic; font-size: 12.5px; color: var(--muted); line-height: 1.5; }
</style>
</head>
<body>
<main class="sheet">

  <section class="card card-front" aria-label="Business card front">
    <div class="backdrop"></div>
    <svg class="swoosh" viewBox="0 0 680 416" preserveAspectRatio="none" aria-hidden="true">
      <path d="M200 0 C300 190 520 275 680 330 L680 300 C520 250 330 170 225 0 Z" fill="var(--charcoal)"/>
      <path d="M225 0 H680 V300 C520 250 330 170 225 0 Z" fill="var(--white)"/>
    </svg>

    <div class="brand">
      <span class="brand-dot"></span>
      <span class="brand-name">
        <span class="line-1">Harbourline</span>
        <span class="line-2">Physiotherapy</span>
      </span>
    </div>

    <div class="holder">
      <p class="holder-name">Daniel Reeve</p>
      <p class="holder-role">CEO/Founder</p>
    </div>

    <ul class="contact">
      <li class="address">58 Wexley Lane Brooksvale<br>NSW 2841</li>
      <li><svg viewBox="0 0 24 24"><path d="M6.6 10.8a15 15 0 0 0 6.6 6.6l2.2-2.2c.3-.3.7-.4 1-.2 1.1.4 2.3.6 3.6.6.6 0 1 .4 1 1V20c0 .6-.4 1-1 1A17 17 0 0 1 3 4c0-.6.4-1 1-1h3.5c.6 0 1 .4 1 1 0 1.3.2 2.5.6 3.6.1.3 0 .7-.2 1z"/></svg>02 9481 2057</li>
      <li><svg viewBox="0 0 24 24"><path d="M6 2h10v5H6zM3 9h18v10h-3v3H6v-3H3zm5 7v4h8v-4z"/></svg>02 9481 2057</li>
      <li><svg viewBox="0 0 24 24"><path d="M2 5h20v14H2zm2 2v.5l8 5 8-5V7z"/></svg>info@harbourlinephysio.example.com.au</li>
      <li><svg viewBox="0 0 24 24"><path d="M12 2a10 10 0 1 0 0 20 10 10 0 0 0 0-20zm0 2c1.2 1.4 2 3.5 2.2 6H9.8c.2-2.5 1-4.6 2.2-6zM4.1 13h3.7c.1 2 .6 3.8 1.4 5.3A8 8 0 0 1 4.1 13zm0-2a8 8 0 0 1 5.1-6.3c-.8 1.5-1.3 3.3-1.4 6.3zm5.7 2h4.4c-.2 2.5-1 4.6-2.2 6-1.2-1.4-2-3.5-2.2-6zm6.4 0h3.7a8 8 0 0 1-5.1 5.3c.8-1.5 1.3-3.3 1.4-5.3zm0-2c-.1-3-.6-4.8-1.4-6.3A8 8 0 0 1 19.9 11z"/></svg>www.harbourlinephysio.example.com.au</li>
    </ul>
  </section>

  <section class="card card-back" aria-label="Business card back – appointment reminder">
    <h2 class="appt-title">Next Appointment</h2>
    <div class="field-row"><span class="fill-line"></span><span>has an appointment</span></div>
    <div class="field-row time-row">
      <span class="label">Time :</span><span class="fill-line"></span><span class="unit">AM/PM</span>
    </div>
    <ul class="days">
      <li>Mon <span class="tick-box"></span></li>
      <li>Tue <span class="tick-box"></span></li>
      <li>Wed <span class="tick-box"></span></li>
      <li>Thu <span class="tick-box"></span></li>
      <li>Fri <span class="tick-box"></span></li>
      <li>Sat <span class="tick-box"></span></li>
    </ul>
    <p class="policy">Please give 24 hours notice if you are unable to keep your appointment or<br>a cancellation fee may be charged.</p>
  </section>

</main>
</body>
</html>
```